Commercial, Public Works, Contractor needs a modern web design

We are a General and Engineering contracting firm with vast experience in our industry. Our focus is on Commercial, Tenant Improvement, Restaurants, and Public Works. We are opening a new business and would like that excitement and energy to show through the new web design. The colors we like are black, red and grey, we are open to color ideas. Attached is our logo design.

Industry/Entity Type

Restaurant

```html
<!DOCTYPE html>
<html lang="en">
<head>
<meta charset="utf-8">
<title>K R Halden, Inc. — General Engineering Contracting Firm</title>
<link href="https://fonts.googleapis.com/css2?family=Raleway:wght@300;400;500&family=Open+Sans:ital,wght@0,400;0,600;0,700;1,400&display=swap" rel="stylesheet">
<style>
  :root {
    --red: #c4161c;
    --red-dark: #a91016;
    --ink: #2b2b2b;
    --text: #555;
    --muted: #888;
    --grey-btn: #9a9a9a;
    --rule: #e4e4e4;
    --panel: #f2f2f2;
    --nav: #3b3b3b;
    --footer: #3d3d3d;
    --white: #fff;
  }
  * { box-sizing: border-box; margin: 0; padding: 0; }
  html, body { width: 700px; height: 1200px; overflow: hidden; background: var(--white); }
  body { position: relative; font-family: "Open Sans", Arial, sans-serif; color: var(--text); }
  .abs { position: absolute; }

  /* header */
  .site-header { left: 0; top: 0; width: 700px; height: 67px; background: linear-gradient(#fff, #f4f4f4); }
  .brand { left: 76px; top: 22px; display: flex; align-items: center; gap: 7px; }
  .brand-mark { width: 20px; height: 20px; border-radius: 50%; background: var(--red); }
  .brand-name { font-family: "Open Sans", Arial, sans-serif; font-weight: 700; font-size: 14px; color: var(--red); letter-spacing: .3px; }
  .social-top { right: 78px; top: 27px; display: flex; gap: 5px; }
  .social-top span { width: 18px; height: 18px; border-radius: 50%; }
  .social-top span:nth-child(1) { background: #2d5da8; }
  .social-top span:nth-child(2) { background: #2fa6d9; }
  .social-top span:nth-child(3) { background: #f3a531; }
  .social-top span:nth-child(4) { background: #c9372c; }

  /* nav */
  .main-nav { left: 0; top: 67px; width: 700px; height: 30px; background: linear-gradient(#4a4a4a, #2f2f2f); }
  .main-nav ul { list-style: none; display: flex; height: 100%; padding-left: 76px; }
  .main-nav li { font-size: 7.5px; color: var(--white); text-transform: uppercase; display: flex; align-items: center; height: 100%; }
  .main-nav li.active { background: var(--red); width: 62px; justify-content: center; }
  .main-nav li + li { margin-left: 17px; }
  .main-nav li.wide { margin-left: 33px; }

  /* hero */
  .hero { left: 0; top: 97px; width: 700px; height: 255px; background: linear-gradient(180deg, #6f7378 0%, #a9adb1 45%, #c9c9c6 70%, #8c8c88 100%); }
  .hero-title { left: 310px; top: 150px; font-family: "Raleway", sans-serif; font-weight: 400; font-size: 20.5px; line-height: 28.5px; color: var(--red); }
  .hero-text { left: 311px; top: 223px; width: 320px; font-size: 8px; line-height: 16.5px; color: #1f1f1f; font-weight: 600; }
  .hero-arrow { top: 221px; width: 25px; height: 25px; background: rgba(235,235,235,.85); }
  .hero-arrow svg { display: block; margin: 7px auto; }

  /* section headings */
  .section-title { left: 0; width: 700px; text-align: center; font-family: "Raleway", sans-serif; font-weight: 400; font-size: 18px; color: var(--ink); }
  .welcome-text { left: 90px; top: 414px; width: 520px; text-align: center; font-size: 7.3px; line-height: 16px; color: var(--text); }
  .btn { display: flex; align-items: center; justify-content: center; width: 68px; height: 23px; font-size: 7.5px; font-weight: 600; color: var(--white); background: var(--red); }
  .btn.grey { background: var(--grey-btn); width: 68px; }
  .rule { left: 76px; width: 549px; height: 1px; background: var(--rule); }
  .services-lead { left: 0; width: 700px; top: 567px; text-align: center; font-size: 8.4px; color: var(--ink); }

  /* service cards */
  .service-photo { width: 128px; height: 84px; }
  .service-title { font-family: "Open Sans", Arial, sans-serif; font-size: 12.3px; color: var(--red); }
  .service-text { width: 130px; font-size: 7.2px; line-height: 14px; color: var(--text); }

  /* testimonials */
  .quote { top: 962px; width: 165px; height: 80px; background: var(--panel); padding: 12px 12px; font-size: 7.2px; line-height: 14px; color: var(--text); }
  .quote::after { content: ""; position: absolute; left: 20px; bottom: -9px; border-left: 8px solid transparent; border-right: 8px solid transparent; border-top: 9px solid var(--panel); }
  .avatar { top: 1060px; width: 43px; height: 43px; border-radius: 50%; border: 2px solid #ddd; background: linear-gradient(135deg, #d9b89b, #8d6a55); }
  .person-name { top: 1070px; font-size: 7px; font-weight: 700; color: var(--red); text-transform: uppercase; }
  .person-role { top: 1081px; font-size: 7px; font-style: italic; color: var(--muted); }

  /* footer */
  .site-footer { left: 0; top: 1133px; width: 700px; height: 67px; background: var(--footer); }
  .footer-links { left: 78px; top: 1153px; font-size: 7.3px; color: var(--white); display: flex; gap: 7px; }
  .footer-links .sep { color: #bbb; }
  .copyright { left: 78px; top: 1171px; font-size: 7px; color: #e0e0e0; }
  .social-foot { left: 523px; top: 1160px; display: flex; gap: 3px; }
  .social-foot span { width: 18px; height: 18px; border-radius: 50%; background: var(--white); }
</style>
</head>
<body>
  <header class="abs site-header">
    <div class="abs brand"><span class="brand-mark"></span><span class="brand-name">K R HALDEN, INC.</span></div>
    <div class="abs social-top" aria-label="Social links"><span></span><span></span><span></span><span></span></div>
  </header>

  <nav class="abs main-nav">
    <ul>
      <li class="active">Home</li>
      <li>About Us</li>
      <li class="wide">&#9662; Services</li>
      <li class="wide">Testimonials</li>
      <li class="wide">Our Works</li>
      <li class="wide">Blog</li>
      <li class="wide">Contact Us</li>
    </ul>
  </nav>

  <section class="abs hero" role="img" aria-label="Silhouette of an engineer with a briefcase beside a steel frame structure at dusk"></section>
  <h1 class="abs hero-title">GENERAL ENGINEERING<br>CONTRACTING FIRM</h1>
  <p class="abs hero-text">Neque porro quisquam est qui dolorem ipsum quia dolor sit amet, consectetur, adipisci velit..Neque porro quisquam est qui dolorem ipsum quia dolor sit amet, consectetur, adipisci velit..</p>
  <div class="abs hero-arrow" style="left:0"><svg width="8" height="10" viewBox="0 0 8 10"><path d="M6 1 L2 5 L6 9" fill="none" stroke="#888" stroke-width="1.3"/></svg></div>
  <div class="abs hero-arrow" style="left:675px"><svg width="8" height="10" viewBox="0 0 8 10"><path d="M2 1 L6 5 L2 9" fill="none" stroke="#333" stroke-width="1.3"/></svg></div>

  <h2 class="abs section-title" style="top:378px">Welcome to Our Site</h2>
  <p class="abs welcome-text">Lorem ipsum dolor sit amet, consectetur adipiscing elit, sed do eiusmod tempor incididunt ut labore et dolore magna aliqua. Ut enim ad minim veniam, quis nostrud exercitation ullamco laboris nisi ut aliquip ex ea commodo consequat. Lorem ipsum dolor sit amet, consectetur adipiscing elit, sed do eiusmod tempor incididunt ut labore et dolore magna aliqua.</p>
  <a class="abs btn" style="left:316px;top:473px">Read More</a>
  <div class="abs rule" style="top:515px"></div>

  <h2 class="abs section-title" style="top:535px">Our Services</h2>
  <p class="abs services-lead">Our focus is on Commercial, Tenant Improvement, Restaurants, and Public Works.</p>

  <div class="abs service-photo" style="left:76px;top:617px;background:linear-gradient(135deg,#dfe3e6,#e89a3a 55%,#8a9aa8)" role="img" aria-label="Two engineers in hard hats reviewing plans"></div>
  <h3 class="abs service-title" style="left:216px;top:614px">Commercial</h3>
  <p class="abs service-text" style="left:217px;top:638px">Lorem ipsum dolor sit amet, consectetur adipiscing elit, sed do eiusmod tempor incididunt ut labore et dolore magna aliqua.</p>
  <a class="abs btn" style="left:217px;top:703px">Read More</a>

  <div class="abs service-photo" style="left:356px;top:617px;background:linear-gradient(135deg,#1f2225,#3a3d40 55%,#c9a46a)" role="img" aria-label="Wooden house model on blueprints"></div>
  <h3 class="abs service-title" style="left:496px;top:612px">Tenant Improvement</h3>
  <p class="abs service-text" style="left:496px;top:635px">Lorem ipsum dolor sit amet, consectetur adipiscing elit, sed do eiusmod tempor incididunt ut labore et dolore magna aliqua.</p>
  <a class="abs btn grey" style="left:497px;top:702px">Read More</a>

  <div class="abs service-photo" style="left:76px;top:762px;background:linear-gradient(180deg,#a8322a,#6b3a2a 50%,#c9b49a)" role="img" aria-label="Restaurant dining room interior"></div>
  <h3 class="abs service-title" style="left:216px;top:758px">Restaurants</h3>
  <p class="abs service-text" style="left:217px;top:782px">Lorem ipsum dolor sit amet, consectetur adipiscing elit, sed do eiusmod tempor incididunt ut labore et dolore magna aliqua.</p>
  <a class="abs btn grey" style="left:217px;top:847px">Read More</a>

  <div class="abs service-photo" style="left:356px;top:761px;background:linear-gradient(135deg,#3a3c3e,#5c5e5c 50%,#7fb13c)" role="img" aria-label="Road workers marking an asphalt surface"></div>
  <h3 class="abs service-title" style="left:496px;top:756px">Public Works</h3>
  <p class="abs service-text" style="left:496px;top:779px">Lorem ipsum dolor sit amet, consectetur adipiscing elit, sed do eiusmod tempor incididunt ut labore et dolore magna aliqua.</p>
  <a class="abs btn grey" style="left:497px;top:846px">Read More</a>

  <div class="abs rule" style="top:895px"></div>

  <h2 class="abs section-title" style="top:924px">Testimonials</h2>

  <blockquote class="abs quote" style="left:77px">Lorem ipsum dolor sit amet, consectetur adipiscing elit, sed do eiusmod tempoer incididunt ut labore et dolore magna sit aliqua sed do eiusmod.</blockquote>
  <div class="abs avatar" style="left:80px" role="img" aria-label="Client portrait"></div>
  <div class="abs person-name" style="left:132px">Marco</div>
  <div class="abs person-role" style="left:132px">dolore magna aliqua</div>

  <blockquote class="abs quote" style="left:268px">Lorem ipsum dolor sit amet, consectetur adipiscing elit, sed do eiusmod tempoer incididunt ut labore et dolore magna sit aliqua sed do eiusmod.</blockquote>
  <div class="abs avatar" style="left:271px" role="img" aria-label="Client portrait"></div>
  <div class="abs person-name" style="left:323px">Lena</div>
  <div class="abs person-role" style="left:323px">dolore magna aliqua</div>

  <blockquote class="abs quote" style="left:458px">Lorem ipsum dolor sit amet, consectetur adipiscing elit, sed do eiusmod tempoer incididunt ut labore et dolore magna sit aliqua sed do eiusmod.</blockquote>
  <div class="abs avatar" style="left:461px" role="img" aria-label="Client portrait"></div>
  <div class="abs person-name" style="left:513px">Sadia</div>
  <div class="abs person-role" style="left:513px">dolore magna aliqua</div>

  <footer class="abs site-footer"></footer>
  <div class="abs footer-links"><span>Home</span><span class="sep">|</span><span>About us</span><span class="sep">|</span><span>Site map</span><span class="sep">|</span><span>Contact us</span></div>
  <p class="abs copyright">©2014. Yoursite. All Right Reserved.</p>
  <div class="abs social-foot" aria-label="Social links"><span></span><span></span><span></span><span></span><span></span></div>
</body>
</html>
```